Makers' Hollow - Landing page for small and large screen

Makers’ Hollow gives you the space you need to take your side project from idea to reality.

With three days of focused work, it’s a place for you iron out the details of your business idea away from the distractions of the city.

The full copy and structure is here:
https://www.makershollow.co.uk/landing

What it needs, a touch of colour.

Target Market(s)

25-35 working in digital industry, software developer, a UI or UX designer

Number of Pages Required

1 page

Font styles to use
Sans Serif

Colors
0292cd
33b8a4
86cfc6
fdf9cf
ec1f27

Requirements
Should not have
• gradients or too much images

```html
<!DOCTYPE html>
<html lang="en">
<head>
<meta charset="utf-8">
<title>Makers’ Hollow</title>
<link rel="stylesheet" href="https://fonts.googleapis.com/css2?family=Lato:ital,wght@0,400;0,700;1,400;1,700&family=Montserrat:wght@400;700&family=Raleway:wght@300;400&display=swap">
<style>
  :root {
    --blue: #0292cd;
    --teal: #33b8a4;
    --mint: #86cfc6;
    --cream: #fdf9cf;
    --red: #ec1f27;
    --ice: #d5eef9;
    --ink: #222;
    --muted: #555;
    --footer: #2b2b2b;
    --white: #fff;
  }
  * { margin: 0; padding: 0; box-sizing: border-box; }
  html, body { width: 1200px; height: 3416px; overflow: hidden; }
  body { position: relative; background: var(--white); font-family: "Lato", sans-serif; color: var(--ink); }
  .abs { position: absolute; }

  .hero { left: 0; top: 0; width: 1200px; height: 622px; overflow: hidden; }
  .hero-photo { position: absolute; inset: 0; background: linear-gradient(100deg, #cfcfc4 0%, #a7a396 30%, #6e5c4c 60%, #3b2e26 100%); }
  .brand { position: absolute; left: 114px; top: 64px; font-family: "Montserrat", sans-serif; font-weight: 700; font-size: 30px; color: var(--white); letter-spacing: 1px; }
  .menu-btn { position: absolute; left: 1031px; top: 56px; width: 56px; height: 56px; border: 3px solid var(--white); border-radius: 50%; }
  .menu-btn span { position: absolute; left: 16px; width: 18px; height: 3px; background: var(--white); border-radius: 2px; }
  .tagline-band { position: absolute; left: 0; top: 542px; width: 940px; height: 80px; background: var(--blue); clip-path: polygon(0 0, 100% 0, 97% 100%, 0 100%); }
  .tagline { position: absolute; left: 42px; top: 548px; font-family: "Montserrat", sans-serif; font-weight: 700; font-size: 52px; color: var(--white); letter-spacing: 1px; }

  .intro-title { left: 0; top: 742px; width: 1200px; text-align: center; font-family: "Montserrat", sans-serif; font-size: 32px; line-height: 42px; color: var(--ink); }
  .intro-title em { font-style: normal; color: var(--blue); }
  .intro-copy { left: 200px; top: 852px; width: 800px; text-align: center; font-size: 14px; line-height: 36px; color: var(--muted); }
  .intro-lead { left: 260px; top: 1050px; width: 680px; text-align: center; font-size: 19px; line-height: 36px; font-style: italic; color: var(--ink); }

  .btn { display: flex; align-items: center; justify-content: center; background: var(--red); color: var(--white); font-weight: 700; text-transform: uppercase; border-radius: 28px; }
  .btn-more { left: 505px; top: 1164px; width: 191px; height: 55px; font-size: 14px; }
  .rule { left: 109px; top: 1339px; width: 979px; height: 1px; background: #e6e6e6; }

  .section-title { left: 0; width: 1200px; text-align: center; font-family: "Raleway", sans-serif; font-weight: 300; font-size: 38px; color: var(--blue); text-transform: uppercase; }
  .perks-title { top: 1440px; }
  .perks-art { left: 0; top: 1560px; width: 1200px; height: 600px; }
  .perk { width: 170px; text-align: center; font-size: 14px; line-height: 22px; color: var(--ink); }
  .perk-main { left: 499px; top: 1746px; width: 200px; font-size: 22px; line-height: 33px; color: var(--white); text-align: center; }

  .organisers { left: 0; top: 2252px; width: 1200px; height: 517px; background: var(--teal); }
  .organisers-title { top: 2366px; color: var(--white); }
  .avatar { left: 166px; top: 2478px; width: 168px; height: 168px; border-radius: 50%; background: radial-gradient(circle at 50% 40%, #7a7a7a, #2a2a2a 70%); }
  .organiser-name { left: 360px; top: 2478px; font-size: 19px; font-weight: 700; color: var(--white); letter-spacing: 1px; }
  .organiser-bio { left: 360px; top: 2516px; width: 680px; font-size: 13.5px; line-height: 29px; font-style: italic; font-weight: 700; color: var(--white); }
  .organiser-links { left: 362px; top: 2618px; display: flex; gap: 12px; }
  .organiser-links span { width: 16px; height: 16px; border: 2px solid var(--white); border-radius: 3px; }
  .carousel-arrow { top: 2536px; width: 30px; height: 52px; }

  .feedback-title { top: 2886px; }
  .feedback-copy { left: 0; top: 2960px; width: 1200px; text-align: center; font-size: 21px; line-height: 37px; color: var(--ink); }
  .btn-share { left: 455px; top: 3072px; width: 291px; height: 55px; font-size: 17px; }

  .site-footer { left: 0; top: 3263px; width: 1200px; height: 153px; background: var(--footer); }
  .footer-note { left: 109px; top: 3296px; font-size: 11.5px; line-height: 23px; color: var(--white); }
  .copyright { left: 109px; top: 3356px; font-size: 12.5px; color: var(--white); }
  .socials { left: 792px; top: 3313px; display: flex; gap: 12px; }
  .socials span { width: 50px; height: 50px; border: 2px solid #888; border-radius: 50%; display: flex; align-items: center; justify-content: center; }
  .socials i { width: 10px; height: 10px; background: var(--white); border-radius: 50%; }
</style>
</head>
<body>

<header class="abs hero">
  <div class="hero-photo" role="img" aria-label="Photo of a smiling woman in a striped top working on a laptop in a bright café"></div>
  <div class="brand">MAKERS’ HOLLOW</div>
  <div class="menu-btn" aria-label="Menu"><span style="top:17px"></span><span style="top:24px"></span><span style="top:31px"></span></div>
  <div class="tagline-band"></div>
  <div class="tagline">CREATE.CONNECT.COLLABORATE</div>
</header>

<h1 class="abs intro-title">Makers’ Hollow gives you the space you need to take<br><em>your side project from idea to reality.</em></h1>
<div class="abs intro-copy">
  <p>Calling all creatives! Whether you’re a software developer, a UI or UX designer, a product creator or an artworker, you’ll know<br>only too well that great work rarely materialises when you’re in the wrong environment.</p>
  <p>Phones buzzing. Emails pinging. Callbox calls incoming...distractions are everywhere – and they do nothing for your motivation.</p>
  <p>So, if you have a seed of a business idea and need to reclaim some focus, the Makers’ Hollow is for you. Or maybe you’ve<br>created a product, sought a patent and you’re ready – and raring – to go.</p>
</div>
<p class="abs intro-lead">With three days of focused work, it’s a place for you iron out the details of your business idea away from the distractions of the city.</p>
<a class="abs btn btn-more">Read more info</a>
<div class="abs rule"></div>

<h2 class="abs section-title perks-title">Join the retreat and enjoy:</h2>
<svg class="abs perks-art" viewBox="0 1560 1200 600" aria-hidden="true">
  <g fill="var(--ice)">
    <rect x="-78" y="-78" width="156" height="156" rx="12" transform="translate(225 1701) rotate(45)"/>
    <rect x="-78" y="-78" width="156" height="156" rx="12" transform="translate(972 1701) rotate(45)"/>
    <rect x="-78" y="-78" width="156" height="156" rx="12" transform="translate(278 1933) rotate(45)"/>
    <rect x="-78" y="-78" width="156" height="156" rx="12" transform="translate(922 1933) rotate(45)"/>
    <rect x="-78" y="-78" width="156" height="156" rx="12" transform="translate(476 2020) rotate(45)"/>
    <rect x="-78" y="-78" width="156" height="156" rx="12" transform="translate(724 2020) rotate(45)"/>
  </g>
  <rect x="-114" y="-114" width="228" height="228" rx="14" transform="translate(599 1753) rotate(45)" fill="var(--blue)"/>
  <g fill="var(--white)">
    <rect x="572" y="1670" width="56" height="50" rx="3"/>
    <rect x="562" y="1722" width="76" height="5"/>
  </g>
</svg>
<p class="abs perk" style="left:140px;top:1668px">A chance to hone your side project away from the office</p>
<p class="abs perk" style="left:887px;top:1668px">Healthy, low-sugar snacks to get you through the day</p>
<p class="abs perk" style="left:193px;top:1900px">The opportunity to collaborate with likeminded creatives</p>
<p class="abs perk" style="left:837px;top:1911px">Three, nutritious &amp; delicious meals a day</p>
<p class="abs perk" style="left:391px;top:1987px">Good, honest feedback &amp; insight from fellow attendees</p>
<p class="abs perk" style="left:639px;top:1998px">Daily yoga &amp;meditation to help fuel your ideas</p>
<p class="abs perk-main">Three, full days of distraction-free work</p>

<section class="abs organisers"></section>
<h2 class="abs section-title organisers-title">Meet your retreat organisers</h2>
<svg class="abs carousel-arrow" style="left:92px" viewBox="0 0 30 52" aria-label="Previous"><path d="M24 6 6 26l18 20" fill="none" stroke="var(--white)" stroke-width="6" stroke-linecap="round" stroke-linejoin="round"/></svg>
<svg class="abs carousel-arrow" style="left:1078px" viewBox="0 0 30 52" aria-label="Next"><path d="M6 6l18 20L6 46" fill="none" stroke="var(--white)" stroke-width="6" stroke-linecap="round" stroke-linejoin="round"/></svg>
<div class="abs avatar" role="img" aria-label="Portrait photo of organiser Tomas Varga"></div>
<h3 class="abs organiser-name">TOMAS VARGA</h3>
<p class="abs organiser-bio">A software engineer in London, Tomas knows only too well the challenges faced by creatives; it’s the reason he’s organised the Makers’ Hollow, to give everyone the space and time to do their best work. Armed with his trusty camera, photographer Tomas is also a biohacker enthusiast and a thoroughly good egg.</p>
<div class="abs organiser-links"><span></span><span></span><span></span></div>

<h2 class="abs section-title feedback-title">What do you think?</h2>
<p class="abs feedback-copy">Sound good? Keen to know more? Share some feedback via the button below<br>and we can hone the Retreat to suit you.</p>
<a class="abs btn btn-share">Share your thoughts</a>

<footer class="abs site-footer"></footer>
<p class="abs footer-note">GDPR Info: we use Formwell and Postlark to store, process and send your data.<br>Hosting on Hostbay and landing page code on Codeshelf</p>
<p class="abs copyright">Copyright ©2019 Companyname. &nbsp;|&nbsp; Terms and Conditions</p>
<div class="abs socials">
  <span><i></i></span><span><i></i></span><span><i></i></span><span><i></i></span>
  <span><svg width="20" height="15" viewBox="0 0 20 15"><rect width="20" height="15" rx="2" fill="var(--white)"/><path d="M1 2l9 7 9-7" fill="none" stroke="var(--footer)" stroke-width="2"/></svg></span>
</div>

</body>
</html>
```